Luxury Wine Label for New Startup Winery

We need a wine label for our new winery startup. We have worked with a local designer but do not feel the resulting label / logo have the elevation required to present our brand as a luxury wine. Our winery is called "Quailbrook Vineyards" and we are focused on extremely high quality hand crafted artisan and estate wines from the Pacific Northwest.
We would like to see designs that utilize a tree line, or other imagery that represents the "Quailbrook" part of our company name. Another interesting feature could be wood grain.
A logo will be required based on your design so please design with this in mind:
This logo should be consistent with the wine bottle label design, and should be representative of our high end exclusive wine while giving a sense of place (Oregon/ Pacific Northwest.)
I will supply an image of the design we received from our local designer, PLEASE NOTE: in general we do like wood grain and tree line concepts but feel the execution was poorly done.
ATTN: Logo design should be suitable for use on: Bottles (Red wine/rose/white wine), Bussiness cards, vehicle signage, business signage, etc
P.S.:
If you have a design that is not outside the box we are still interested in seeing it.
Label is for a burgundy style bottle with a label height of 3.5 - 4" and a width of 3.5-4"
any label <= 4"x4" and >=3.5"x3.5" will be acceptable:
HOWEVER Width should be greater than or equal to height due to the bottle format
Target Market(s)
Wine enthusiasts with adequate discretionary budgets to afford $100 bottles of wine.
Industry/Entity Type
Wine / Winery
Requirements
Must have
- A sense of luxury, a feel of exclusivity, and a theme consistent with our product and brand name
Nice to have
- Tree line, wood grain or other wood themes. Serif fonts
Should not have
- anything cheesy, off topic, hard to read script fonts or anything that makes the label hard to read from a few feet away or too busy

```html
<!DOCTYPE html>
<html lang="en">
<head>
<meta charset="utf-8">
<title>Quailbrook Vineyard – Label Range</title>
<link href="https://fonts.googleapis.com/css2?family=Cinzel:wght@400&family=Libre+Baskerville:wght@700&family=Montserrat:wght@800&display=swap" rel="stylesheet">
<style>
  :root {
    --maroon: #3d1422;
    --maroon-deep: #2e0e19;
    --grain: #4b1d2d;
    --gold: #f2d24a;
    --gold-dark: #c9a22a;
    --cream: #e6e2cf;
    --ink: #3a1020;
    --syrah: #3a0f1e;
    --rose: #a100c8;
    --white-wine: #cc1a00;
  }
  html, body {
    margin: 0;
    padding: 0;
    width: 1200px;
    height: 300px;
    overflow: hidden;
    background: #ffffff;
  }
  .label-range {
    position: relative;
    width: 1200px;
    height: 300px;
  }
  .label {
    position: absolute;
    top: 0;
    width: 342px;
    height: 300px;
    overflow: hidden;
    background: var(--maroon);
  }
  .label--syrah { left: 0; }
  .label--rose { left: 429px; }
  .label--white { left: 858px; }

  .wood-grain {
    position: absolute;
    inset: 0;
    background: linear-gradient(90deg, var(--maroon-deep), var(--grain) 30%, var(--maroon) 55%, var(--grain) 80%, var(--maroon-deep));
  }
  .ornament-band {
    position: absolute;
    left: 0;
    width: 100%;
    background: linear-gradient(180deg, var(--gold-dark), #8a5a2a 50%, var(--gold-dark));
  }
  .ornament-band--top {
    top: 0;
    height: 12px;
    border-bottom: 2px solid var(--gold);
  }
  .ornament-band--bottom {
    top: 259px;
    height: 41px;
    border-top: 2px solid var(--gold);
    box-sizing: border-box;
  }

  .brand {
    position: absolute;
    top: 40px;
    left: 0;
    width: 100%;
    text-align: center;
    color: var(--gold);
    font-family: "Montserrat", sans-serif;
    font-weight: 800;
  }
  .brand__mark {
    display: block;
    width: 34px;
    height: 34px;
    margin: 0 auto 40px;
    background: var(--gold);
  }
  .brand__name {
    display: block;
    font-size: 31px;
    line-height: 1;
    letter-spacing: 0.5px;
  }
  .brand__sub {
    display: block;
    margin-top: 6px;
    font-size: 15px;
    letter-spacing: 6px;
    line-height: 1;
  }

  .origin-band {
    position: absolute;
    top: 216px;
    left: 0;
    width: 100%;
    height: 43px;
    background: var(--cream);
    text-align: center;
    color: var(--ink);
    font-family: "Libre Baskerville", serif;
    font-weight: 700;
  }
  .origin-band__region {
    display: block;
    margin-top: 7px;
    font-size: 12px;
    letter-spacing: 0.3px;
  }
  .origin-band__vintage {
    display: block;
    margin-top: 3px;
    font-size: 10px;
  }

  .varietal {
    position: absolute;
    top: 259px;
    left: 98px;
    width: 144px;
    height: 41px;
    display: flex;
    align-items: center;
    justify-content: center;
    font-family: "Cinzel", serif;
    font-weight: 400;
    font-size: 25px;
    color: var(--gold);
    letter-spacing: 0.5px;
  }
  .varietal--syrah { background: var(--syrah); }
  .varietal--rose { background: var(--rose); }
  .varietal--white { background: var(--white-wine); }
</style>
</head>
<body>
<main class="label-range">

  <section class="label label--syrah">
    <div class="wood-grain" role="img" aria-label="Dark burgundy wood grain texture"></div>
    <div class="ornament-band ornament-band--top" role="img" aria-label="Gold filigree ornament border"></div>
    <div class="brand">
      <span class="brand__mark"></span>
      <span class="brand__name">QUAILBROOK</span>
      <span class="brand__sub">VINEYARD</span>
    </div>
    <div class="origin-band">
      <span class="origin-band__region">WILLAMETTE VALLEY</span>
      <span class="origin-band__vintage">-2024-</span>
    </div>
    <div class="ornament-band ornament-band--bottom" role="img" aria-label="Gold filigree ornament border"></div>
    <div class="varietal varietal--syrah">SYRAH</div>
  </section>

  <section class="label label--rose">
    <div class="wood-grain" role="img" aria-label="Dark burgundy wood grain texture"></div>
    <div class="ornament-band ornament-band--top" role="img" aria-label="Gold filigree ornament border"></div>
    <div class="brand">
      <span class="brand__mark"></span>
      <span class="brand__name">QUAILBROOK</span>
      <span class="brand__sub">VINEYARD</span>
    </div>
    <div class="origin-band">
      <span class="origin-band__region">WILLAMETTE VALLEY</span>
      <span class="origin-band__vintage">-2024-</span>
    </div>
    <div class="ornament-band ornament-band--bottom" role="img" aria-label="Gold filigree ornament border"></div>
    <div class="varietal varietal--rose">ROSE</div>
  </section>

  <section class="label label--white">
    <div class="wood-grain" role="img" aria-label="Dark burgundy wood grain texture"></div>
    <div class="ornament-band ornament-band--top" role="img" aria-label="Gold filigree ornament border"></div>
    <div class="brand">
      <span class="brand__mark"></span>
      <span class="brand__name">QUAILBROOK</span>
      <span class="brand__sub">VINEYARD</span>
    </div>
    <div class="origin-band">
      <span class="origin-band__region">WILLAMETTE VALLEY</span>
      <span class="origin-band__vintage">-2024-</span>
    </div>
    <div class="ornament-band ornament-band--bottom" role="img" aria-label="Gold filigree ornament border"></div>
    <div class="varietal varietal--white">WHITE</div>
  </section>

</main>
</body>
</html>
```